Corvane Capital Business Cards

These are professional business cards that are for my family office.
Put fake emails and phone numbers as of now until I finalize those components. This family office controls my families investments, assets, and future. The cards should be professional.
..
.
.
.
I just uploaded another variation of a logo I would like to see as a business card to I am inbeteen which logo to use

Target Market(s)

business

Industry/Entity Type

business

Contact Information for Business Card

Professional, wealth related, finance related.

Requirements
Must have
• Logo

```html
<!DOCTYPE html>
<html lang="en">
<head>
<meta charset="utf-8">
<title>Corvane Capital Business Cards</title>
<link rel="stylesheet" href="https://fonts.googleapis.com/css2?family=Cinzel:wght@400&family=Montserrat:wght@400;700&display=swap">
<style>
  :root {
    --navy: #1a1f2c;
    --white: #ffffff;
    --stage: #e9e7e3;
    --ink: #1a1f2c;
  }
  * { box-sizing: border-box; margin: 0; padding: 0; }
  html, body {
    width: 900px; height: 1200px; overflow: hidden;
    background: var(--stage);
  }
  .canvas { position: relative; width: 900px; height: 1200px; }
  .card {
    position: absolute;
    width: 742px; height: 440px;
    border-radius: 24px;
    overflow: hidden;
  }
  .card--front { left: 80px; top: 131px; background: var(--white); color: var(--ink); }
  .card--back  { left: 79px; top: 638px; background: var(--navy); color: var(--white); }

  .wordmark {
    font-family: "Cinzel", serif;
    font-weight: 400;
    letter-spacing: 1px;
    white-space: nowrap;
  }
  .card--front .wordmark {
    position: absolute; left: 28px; top: 44px;
    font-size: 38px; color: var(--navy);
  }
  .front-ring {
    position: absolute; left: 0; top: 0;
  }
  .holder { position: absolute; left: 28px; top: 156px; font-family: "Montserrat", sans-serif; }
  .holder__name { font-size: 25px; font-weight: 700; line-height: 1.2; }
  .holder__role { font-size: 15px; font-weight: 400; margin-top: 2px; }

  .address {
    position: absolute; left: 28px; top: 250px;
    font-family: "Montserrat", sans-serif; font-size: 15.5px; line-height: 20px;
  }
  .contacts {
    position: absolute; left: 28px; top: 326px;
    list-style: none;
    font-family: "Montserrat", sans-serif; font-size: 15.5px;
  }
  .contacts li { display: flex; align-items: center; height: 28px; }
  .contacts svg { width: 15px; height: 15px; margin-right: 10px; fill: var(--navy); }

  .back-ring { position: absolute; left: 262px; top: 70px; }
  .card--back .wordmark {
    position: absolute; left: 0; right: 0; top: 318px;
    text-align: center; font-size: 42px;
  }
</style>
</head>
<body>
<main class="canvas">
  <section class="card card--front" aria-label="Business card front">
    <svg class="front-ring" width="742" height="440" viewBox="0 0 742 440" aria-hidden="true">
      <circle cx="690" cy="220" r="212" fill="none" stroke="var(--navy)" stroke-width="7"/>
    </svg>
    <div class="wordmark">Corvane Capital</div>
    <div class="holder">
      <div class="holder__name">Martin Okafor</div>
      <div class="holder__role">Owner</div>
    </div>
    <address class="address" style="font-style:normal">
      42 Linden Court<br>Fairhaven, NJ 07011 USA
    </address>
    <ul class="contacts">
      <li>
        <svg viewBox="0 0 24 24" aria-hidden="true"><path d="M6.6 10.8a15.1 15.1 0 0 0 6.6 6.6l2.2-2.2a1 1 0 0 1 1-.25 11.4 11.4 0 0 0 3.6.57 1 1 0 0 1 1 1V20a1 1 0 0 1-1 1A17 17 0 0 1 3 4a1 1 0 0 1 1-1h3.5a1 1 0 0 1 1 1c0 1.25.2 2.45.57 3.57a1 1 0 0 1-.25 1z"/></svg>
        (555)201-4478
      </li>
      <li>
        <svg viewBox="0 0 24 24" aria-hidden="true"><path d="M2 5h20v2l-10 6L2 7z"/><path d="M2 9l10 6 10-6v10H2z"/></svg>
        info@corvanecapital-demo.com
      </li>
      <li>
        <svg viewBox="0 0 24 24" aria-hidden="true"><path d="M12 2a10 10 0 1 0 0 20 10 10 0 0 0 0-20zm6.9 6h-3a15.6 15.6 0 0 0-1.4-3.6A8 8 0 0 1 18.9 8zM12 4c.8 1.2 1.5 2.5 1.9 4h-3.8c.4-1.5 1.1-2.8 1.9-4zM4.3 14a8 8 0 0 1 0-4h3.4a16 16 0 0 0 0 4zm.8 2h3a15.6 15.6 0 0 0 1.4 3.6A8 8 0 0 1 5.1 16zm3-8h-3a8 8 0 0 1 4.4-3.6A15.6 15.6 0 0 0 8.1 8zM12 20c-.8-1.2-1.5-2.5-1.9-4h3.8c-.4 1.5-1.1 2.8-1.9 4zm2.3-6H9.7a14.6 14.6 0 0 1 0-4h4.6a14.6 14.6 0 0 1 0 4zm.2 5.6a15.6 15.6 0 0 0 1.4-3.6h3a8 8 0 0 1-4.4 3.6zM16.3 14a16 16 0 0 0 0-4h3.4a8 8 0 0 1 0 4z"/></svg>
        www.corvanecapital-demo.com
      </li>
    </ul>
  </section>

  <section class="card card--back" aria-label="Business card back">
    <svg class="back-ring" width="220" height="220" viewBox="0 0 220 220" aria-hidden="true">
      <circle cx="110" cy="110" r="106" fill="none" stroke="var(--white)" stroke-width="5"/>
    </svg>
    <div class="wordmark">Corvane Capital</div>
  </section>
</main>
</body>
</html>
```